Verodex business card

Business card for sustainable investment company called "Verodex". Verodex is an exchange platform selling carbon credits between buyers and sellers. Carbon Credits are an environmental commodity for reducing global carbon emissions.

the card should obviously have our logo and the theme should be sustainability/environment mixed with a trading platform.

Contact Information for Business Card

Logo, Name, Title, Phone, Email

Colors
0054AA
0677BA
7BADD7
CADEEF
E8F1F8
0094D4
00A9DD
6FCCEA
C7EBF8
E9F6FB
00AB8E
00BBA5
67D7C9
C6EFE9
E9F9F6
59FF00
82FF00
B8FF75
E3FFCB
F4FFEA

```html
<!DOCTYPE html>
<html lang="en">
<head>
<meta charset="utf-8">
<title>Verodex business card</title>
<link rel="stylesheet" href="https://fonts.googleapis.com/css2?family=Montserrat:wght@400;500;600;700&display=swap">
<style>
  :root {
    --navy: #142a55;
    --blue: #0054aa;
    --sky: #00a9dd;
    --sky-light: #6fccea;
    --ink: #1b2a48;
    --paper: #ffffff;
    --backdrop: #e9ecf1;
  }
  * { box-sizing: border-box; margin: 0; padding: 0; }
  html, body {
    width: 1200px; height: 900px; overflow: hidden;
    background: var(--backdrop);
    font-family: "Montserrat", sans-serif;
  }
  .canvas { position: relative; width: 1200px; height: 900px; }
  .card {
    position: absolute; left: 250px; width: 700px; height: 400px;
    box-shadow: 0 6px 20px rgba(20, 30, 60, 0.18);
    overflow: hidden;
  }
  .card--front { top: 40px; background: var(--navy); }
  .card--back { top: 460px; background: var(--paper); }

  .brand { display: flex; align-items: center; gap: 22px; }
  .brand__dot { width: 62px; height: 62px; border-radius: 50%; background: var(--sky); }
  .brand__name { font-weight: 600; letter-spacing: 2px; line-height: 1; }
  .card--front .brand {
    position: absolute; inset: 0; justify-content: center;
  }
  .card--front .brand__name { color: var(--paper); font-size: 70px; }

  .card--back .brand { position: absolute; left: 110px; top: 52px; }
  .card--back .brand__dot { width: 56px; height: 56px; }
  .card--back .brand__name { color: var(--ink); font-size: 58px; }

  .wave { position: absolute; inset: 0; }

  .details {
    position: absolute; left: 95px; top: 145px;
    display: flex; align-items: stretch; gap: 16px;
  }
  .person { text-align: right; padding-top: 8px; }
  .person__name { font-size: 22px; font-weight: 700; letter-spacing: 0.5px; }
  .person__first { color: var(--sky); }
  .person__last { color: var(--ink); }
  .person__title { font-size: 16px; font-weight: 500; color: var(--ink); margin-top: 4px; }
  .divider { width: 2px; background: var(--sky); }
  .contacts { list-style: none; display: flex; flex-direction: column; gap: 7px; }
  .contacts li {
    display: flex; align-items: center; gap: 9px;
    font-size: 15px; font-weight: 500; color: var(--ink);
  }
  .contacts svg { width: 15px; height: 15px; flex: none; }
</style>
</head>
<body>
<main class="canvas">
  <section class="card card--front" aria-label="Card front">
    <div class="brand">
      <span class="brand__dot"></span>
      <span class="brand__name">VERODEX</span>
    </div>
  </section>

  <section class="card card--back" aria-label="Card back">
    <svg class="wave" viewBox="0 0 700 400" preserveAspectRatio="none" aria-hidden="true">
      <defs>
        <linearGradient id="stripe" x1="0" y1="0" x2="1" y2="0">
          <stop offset="0" stop-color="#6fccea"/>
          <stop offset="0.55" stop-color="#00a9dd"/>
          <stop offset="1" stop-color="#0054aa"/>
        </linearGradient>
      </defs>
      <path d="M0,372 C250,370 390,322 495,250 C575,192 625,158 690,146 C630,166 580,198 505,258 C400,335 255,384 0,386 Z" fill="url(#stripe)"/>
      <path d="M0,400 L0,394 C260,392 405,344 510,270 C590,212 645,178 700,168 L700,400 Z" fill="#142a55"/>
    </svg>

    <div class="brand">
      <span class="brand__dot"></span>
      <span class="brand__name">VERODEX</span>
    </div>

    <div class="details">
      <div class="person">
        <p class="person__name"><span class="person__first">DANIEL</span> <span class="person__last">MARSH</span></p>
        <p class="person__title">Co-Founder</p>
      </div>
      <span class="divider"></span>
      <ul class="contacts">
        <li>
          <svg viewBox="0 0 16 16"><path d="M3 1.5h3l1.2 3.2-1.8 1.2a8 8 0 0 0 4.7 4.7l1.2-1.8 3.2 1.2v3a1.5 1.5 0 0 1-1.6 1.5A13 13 0 0 1 1.5 3.1 1.5 1.5 0 0 1 3 1.5z" fill="#00a9dd"/></svg>
          555-210-4386
        </li>
        <li>
          <svg viewBox="0 0 16 16"><rect x="1" y="3" width="14" height="10" rx="1" fill="#0094d4"/><path d="M1.5 3.8 8 9l6.5-5.2" fill="none" stroke="#fff" stroke-width="1.2"/></svg>
          info@verodex.com
        </li>
        <li>
          <svg viewBox="0 0 16 16"><circle cx="8" cy="8" r="7" fill="#0094d4"/><path d="M1 8h14M8 1c2.5 2.5 2.5 11.5 0 14M8 1c-2.5 2.5-2.5 11.5 0 14" fill="none" stroke="#fff" stroke-width="1"/></svg>
          www.verodex.com
        </li>
      </ul>
    </div>
  </section>
</main>
</body>
</html>
```